Kestrelwood Climate Business Card Design

Design new, 2 sides, business cards for a residential and light commercial heating, air conditioning contractor.

Target Market(s)

Homeowners, small businesses

Industry/Entity Type

Business

Contact Information for Business Card

Dominic Westerhall
Phone - 862-415-2736
Email
Address - PO box 518
Brightwater NJ 07912
Website - www.HarborBreezeLLC.example

Requirements
Must have
• logo, company colors, standard size with no die cut, so I can use nova stamp

```html
<!DOCTYPE html>
<html lang="en">
<head>
<meta charset="utf-8">
<title>Kestrelwood Climate Business Cards</title>
<link href="https://fonts.googleapis.com/css2?family=Roboto:wght@400;500;700&family=Roboto+Slab:wght@700&display=swap" rel="stylesheet">
<style>
  :root {
    --bg: #e4e4e4;
    --card: #f5f5f3;
    --maroon: #7d2233;
    --orange: #e8871e;
    --orange-clear: rgba(232,135,30,0);
    --red: #d9301f;
    --gold: #f3c74f;
    --ink: #3a2a2e;
  }
  * { margin: 0; padding: 0; box-sizing: border-box; }
  html, body { width: 1200px; height: 576px; overflow: hidden; }
  body { background: var(--bg); font-family: "Roboto", sans-serif; position: relative; }
  .card {
    position: absolute; top: 138px; width: 485px; height: 294px;
    background: var(--card); overflow: hidden;
    box-shadow: 0 2px 6px rgba(0,0,0,.25);
  }
  .card-front { left: 81px; }
  .card-back { left: 602px; width: 481px; height: 292px; }

  .brand {
    position: absolute; display: flex; align-items: center; gap: 8px;
    color: var(--maroon); font-family: "Roboto", sans-serif; font-weight: 700;
    white-space: nowrap;
  }
  .brand-dot { border-radius: 50%; background: var(--maroon); flex: none; }
  .card-front .brand { left: 50%; top: 134px; transform: translate(-50%, -50%); font-size: 34px; }
  .card-front .brand-dot { width: 24px; height: 24px; }
  .card-back .brand { left: 364px; top: 214px; transform: translate(-50%, -50%); font-size: 20px; }
  .card-back .brand-dot { width: 15px; height: 15px; }

  .service-band {
    position: absolute; left: 0; right: 0; top: 247px; height: 26px;
    background: var(--maroon); color: var(--gold);
    font-size: 12px; display: flex; align-items: center; justify-content: center;
  }

  .header-wave {
    position: absolute; left: 0; top: 0; width: 481px; height: 140px;
    background: linear-gradient(200deg, var(--orange) 0 42%, var(--orange-clear) 72%);
  }
  .services {
    position: absolute; right: 28px; top: 17px; text-align: right;
    font-size: 11.5px; font-weight: 700; color: var(--maroon); line-height: 16px;
    list-style: none;
  }
  .services li span { display: inline-block; width: 14px; text-align: right; font-weight: 400; }
  .services li.plain { padding-right: 14px; }

  .person { position: absolute; left: 20px; top: 68px; }
  .person-name { font-family: "Roboto Slab", serif; font-weight: 700; font-size: 20px; color: var(--maroon); letter-spacing: -0.2px; }
  .person-title { font-size: 10px; color: var(--ink); margin-top: 2px; }

  .contacts { position: absolute; left: 24px; top: 196px; list-style: none; }
  .contacts li { display: flex; align-items: center; gap: 9px; height: 17px; font-size: 12px; color: var(--ink); }
  .contacts svg { width: 11px; height: 11px; fill: var(--red); flex: none; }
</style>
</head>
<body>

<section class="card card-front">
  <div class="brand"><span class="brand-dot"></span>Kestrelwood Climate</div>
  <div class="service-band">Residential &amp; Light Commercial Heating &nbsp;• Air Conditioning Contractor</div>
</section>

<section class="card card-back">
  <div class="header-wave" role="img" aria-label="Decorative orange header with flowing maroon and red wave"></div>
  <ul class="services">
    <li>Residential and Light <span>«</span></li>
    <li class="plain">Commercial Heating</li>
    <li>Air Conditioning <span>«</span></li>
    <li class="plain">Contractor</li>
  </ul>

  <div class="person">
    <div class="person-name">Dominic Westerhall</div>
    <div class="person-title">Managing Director</div>
  </div>

  <ul class="contacts">
    <li><svg viewBox="0 0 12 12"><path d="M1 3.5C1 2 2.5 1 6 1s5 1 5 2.5V5H8.5V3.8H3.5V5H1ZM2.5 6h7l1 5h-9Z"/></svg>862-415-2736</li>
    <li><svg viewBox="0 0 12 12"><path d="M0 2h12v8H0ZM1 3v.5L6 7l5-3.5V3Z" fill-rule="evenodd"/></svg>info@KestrelwoodClimate.example</li>
    <li><svg viewBox="0 0 12 12"><path d="M6 0a4 4 0 0 1 4 4c0 3-4 8-4 8S2 7 2 4a4 4 0 0 1 4-4Zm0 2.5a1.5 1.5 0 1 0 0 3 1.5 1.5 0 0 0 0-3Z" fill-rule="evenodd"/></svg>PO box 518 Brightwater NJ 07912</li>
    <li><svg viewBox="0 0 12 12"><path d="M6 0a6 6 0 1 0 0 12A6 6 0 0 0 6 0Zm-.7 1.2C4.5 2.3 4 4 4 5.4H1.2A4.8 4.8 0 0 1 5.3 1.2Zm1.4 0a4.8 4.8 0 0 1 4.1 4.2H8C8 4 7.5 2.3 6.7 1.2ZM5 5.4c0-1.5.4-2.9 1-3.9.6 1 1 2.4 1 3.9ZM1.2 6.6H4c0 1.4.5 3.1 1.3 4.2A4.8 4.8 0 0 1 1.2 6.6Zm3.8 0h2c0 1.5-.4 2.9-1 3.9-.6-1-1-2.4-1-3.9Zm3 0h2.8a4.8 4.8 0 0 1-4.1 4.2C7.5 9.7 8 8 8 6.6Z" fill-rule="evenodd"/></svg>KestrelwoodClimate.example</li>
  </ul>

  <div class="brand"><span class="brand-dot"></span>Kestrelwood Climate</div>
</section>

</body>
</html>
```